Business Card Design Project

Business Card
We are rebranding with a new logo
Industry/Entity Type
Business
Contact Information for Business Card
Dennis Morvale +61 487215963 dennis@quorv.com.au P.O. Box 872 Fernlow QLD 4309
Requirements
Must have
- Logo

```html
<!DOCTYPE html>
<html lang="en">
<head>
<meta charset="utf-8">
<title>Quorv International – Business Card</title>
<link rel="stylesheet" href="https://fonts.googleapis.com/css2?family=Lato:wght@400;700&display=swap">
<style>
  :root {
    --backdrop: #5a5a5a;
    --card: #ffffff;
    --panel: #000000;
    --ink: #111111;
    --brand-text: #ffffff;
    --accent: #f08a1c;
  }
  * { margin: 0; padding: 0; box-sizing: border-box; }
  html, body {
    width: 1200px;
    height: 926px;
    overflow: hidden;
    background: var(--backdrop);
    font-family: "Lato", sans-serif;
  }
  .business-card {
    position: absolute;
    left: 150px;
    top: 188px;
    width: 900px;
    height: 550px;
    background: var(--card);
    box-shadow: 0 18px 40px rgba(0, 0, 0, 0.35);
  }
  .brand-panel {
    position: absolute;
    inset: 0;
  }
  .brand {
    position: absolute;
    left: 40px;
    top: 248px;
    display: flex;
    align-items: center;
    gap: 12px;
  }
  .brand-dot {
    width: 16px;
    height: 16px;
    border-radius: 50%;
    background: var(--accent);
    flex: none;
  }
  .brand-name {
    color: var(--brand-text);
    font-weight: 700;
    font-size: 20px;
    line-height: 1.2;
    letter-spacing: 2px;
    text-transform: uppercase;
  }
  .contact {
    position: absolute;
    left: 520px;
    top: 292px;
    color: var(--ink);
  }
  .contact-name {
    font-size: 31px;
    font-weight: 400;
    letter-spacing: 0.5px;
    text-transform: uppercase;
  }
  .contact-name strong { font-weight: 700; }
  .rule {
    width: 26px;
    height: 2px;
    background: var(--ink);
    margin: 12px 0 8px;
  }
  .contact-line {
    font-size: 18px;
    line-height: 1.3;
  }
  .contact-line b { font-weight: 700; }
  .address {
    font-size: 21px;
    letter-spacing: 0.3px;
  }
</style>
</head>
<body>
  <section class="business-card">
    <svg class="brand-panel" width="900" height="550" viewBox="0 0 900 550" aria-hidden="true">
      <polygon points="18,18 425,18 185,532 18,532" fill="var(--panel)"/>
    </svg>
    <div class="brand">
      <span class="brand-dot"></span>
      <span class="brand-name">Quorv<br>International</span>
    </div>
    <div class="contact">
      <h1 class="contact-name">Dennis <strong>Morvale</strong></h1>
      <div class="rule"></div>
      <p class="contact-line"><b>T.</b> +61 487215963</p>
      <p class="contact-line"><b>E.</b> dennis@quorv.com.au</p>
      <div class="rule"></div>
      <p class="address">P.O. Box 872 Fernlow QLD 4309</p>
    </div>
  </section>
</body>
</html>
```